Dunmore Roofing

Want a professional looking business card

Industry/Entity Type

Business

Contact Information for Business Card

Paul Dunmore ( Owner) paul@dunmoreroofing-example.com, www.dunmoreroofing-example.com, Adress: 4172 Township road 43 Ashcombe Falls,ON K9X4T2

```html
<!DOCTYPE html>
<html lang="en">
<head>
<meta charset="utf-8">
<title>Dunmore Roofing – Business Card</title>
<link rel="stylesheet" href="https://fonts.googleapis.com/css2?family=Roboto:wght@500;700&family=Ubuntu:wght@400&display=swap">
<style>
  :root {
    --brand-blue: #1f3f86;
    --card-white: #ffffff;
    --text-grey: #4a4a4a;
    --muted-grey: #6b6b6b;
    --backdrop: #d9d9d9;
  }
  * { box-sizing: border-box; margin: 0; padding: 0; }
  html, body { width: 1200px; height: 900px; overflow: hidden; background: var(--backdrop); }
  .canvas {
    position: relative; width: 1200px; height: 900px;
    display: flex; flex-direction: column; align-items: center; justify-content: center; gap: 40px;
  }
  .card {
    position: relative; width: 700px; height: 400px;
    box-shadow: 0 6px 18px rgba(0,0,0,.25);
  }
  .card--back {
    background: var(--brand-blue); color: var(--card-white);
    display: flex; flex-direction: column; align-items: center; justify-content: center;
  }
  .brand-name {
    font-family: "Roboto", sans-serif; font-weight: 700;
    letter-spacing: 3px; text-transform: uppercase; text-align: center; line-height: 1;
  }
  .card--back .brand-name { font-size: 46px; color: var(--card-white); }
  .card--back .website {
    position: absolute; bottom: 38px; left: 0; right: 0; text-align: center;
    font-family: "Ubuntu", sans-serif; font-size: 15px; letter-spacing: 1px; color: var(--card-white);
  }
  .card--front {
    background: var(--card-white);
    display: flex; flex-direction: column; align-items: center; padding-top: 34px;
  }
  .card--front .brand-name { font-size: 40px; color: var(--brand-blue); }
  .holder-name {
    margin-top: 40px; font-family: "Roboto", sans-serif; font-weight: 500;
    font-size: 26px; color: var(--brand-blue);
  }
  .holder-role {
    font-family: "Ubuntu", sans-serif; font-size: 19px; color: var(--muted-grey);
    letter-spacing: 1px; margin-top: 2px;
  }
  .divider { width: 50px; height: 2px; background: var(--brand-blue); margin: 14px 0 12px; }
  .contact-icons { display: flex; gap: 10px; margin-bottom: 12px; }
  .contact-icons svg { width: 14px; height: 14px; fill: var(--brand-blue); }
  .contact-list {
    list-style: none; text-align: center;
    font-family: "Ubuntu", sans-serif; font-size: 18px; letter-spacing: 1.2px;
    color: var(--text-grey); line-height: 1.42;
  }
  .address {
    margin-top: 6px; display: flex; align-items: center; gap: 10px;
    font-family: "Ubuntu", sans-serif; font-size: 18px; letter-spacing: 1px; color: var(--text-grey);
    white-space: nowrap;
  }
  .address svg { width: 18px; height: 18px; fill: var(--brand-blue); flex: none; }
</style>
</head>
<body>
<main class="canvas">
  <section class="card card--back" aria-label="Card back">
    <h1 class="brand-name">Dunmore Roofing</h1>
    <p class="website">www.dunmoreroofing-example.com</p>
  </section>

  <section class="card card--front" aria-label="Card front">
    <h2 class="brand-name">Dunmore Roofing</h2>
    <p class="holder-name">Paul Dunmore</p>
    <p class="holder-role">Owner</p>
    <div class="divider"></div>
    <div class="contact-icons">
      <svg viewBox="0 0 14 14" aria-hidden="true"><path d="M4 0h6a1 1 0 0 1 1 1v12a1 1 0 0 1-1 1H4a1 1 0 0 1-1-1V1a1 1 0 0 1 1-1zm0.5 1.5v10h5v-10z"/></svg>
      <svg viewBox="0 0 14 14" aria-hidden="true"><path d="M0 3h14v1L7 8 0 4zM0 5.5l7 4 7-4V11H0z"/></svg>
      <svg viewBox="0 0 14 14" aria-hidden="true"><path d="M6 1a5 5 0 0 1 4 8l3.5 3.5-1.2 1.2L8.8 10.2A5 5 0 1 1 6 1zm0 2a3 3 0 1 0 0 6 3 3 0 0 0 0-6z"/></svg>
    </div>
    <ul class="contact-list">
      <li>(000)123-4567</li>
      <li>paul@dunmoreroofing-example.com</li>
      <li>www.dunmoreroofing-example.com</li>
    </ul>
    <p class="address">
      <svg viewBox="0 0 18 18" aria-hidden="true"><path d="M17 1 1 8l7 2 2 7z"/></svg>
      4172 Township road 43 Ashcombe Falls,ON K9X4T2
    </p>
  </section>
</main>
</body>
</html>
```